Northvale Strategy Partners Website Design

I need a website design for my new business consulting and executive coaching firm, Northvale Strategy Partners. We provide consultative services to business C-suites as well as personal coaching to executives. I have attached the logo with color scheme I have chosen. I would like the website to reflect professionalism and continue the color scheme in the logo.

Target Market(s)

Small to medium business and their executives; middle to upper income men and women in mid- to late career looking for significance

Industry/Entity Type

Business Consultant

Number of Pages Required

4 page

Requirements
Must have
• A homepage with prominent logo and way to contact for more information; an area on the homepage with easy to read, clear text to describe what the company does; a prominent area on the homepage for a tagline; a blog page that can be updated regularly, an "about us" page with biographical information; an "about us" page; a page detailing services offered
• The web design must match the logo colors and font that I have uploaded.
Nice to have
• A lighthouse picture in the background or header
Should not have
• A lot of text area on the homepage

```html
<!DOCTYPE html>
<html lang="en">
<head>
<meta charset="utf-8">
<title>Northvale Strategy Partners</title>
<link href="https://fonts.googleapis.com/css2?family=Cinzel:wght@400;600&family=Arimo:wght@400;700&family=Roboto+Condensed:wght@400&display=swap" rel="stylesheet">
<style>
:root{
  --bg:#ebe5d7;
  --bg-line:#e2dccd;
  --red:#7d1619;
  --red-dark:#5e0f12;
  --navy:#1b2a5c;
  --blue-btn:#1f6fb0;
  --panel:#f7f6f3;
  --text:#3a3a3a;
  --muted:#8a8a8a;
  --white:#ffffff;
}
*{margin:0;padding:0;box-sizing:border-box}
html,body{width:1200px;height:1021px;overflow:hidden}
body{position:relative;background:var(--bg);
  background-image:repeating-linear-gradient(0deg,transparent 0 3px,var(--bg-line) 3px 4px),repeating-linear-gradient(90deg,transparent 0 4px,rgba(0,0,0,.015) 4px 5px);
  font-family:'Arimo',sans-serif;color:var(--text)}
.abs{position:absolute}
.contact-line{right:132px;top:32px;font-family:'Cinzel',serif;font-size:22px;color:var(--red);letter-spacing:.5px}
.nav-band{left:0;top:78px;width:1200px;height:48px;background:var(--red);border-top:2px solid var(--red-dark);border-bottom:2px solid var(--red-dark);box-shadow:0 2px 3px rgba(0,0,0,.2)}
.nav-band::before{content:"";position:absolute;left:0;right:0;top:3px;border-top:1px dashed rgba(255,255,255,.35)}
.nav-band::after{content:"";position:absolute;left:0;right:0;bottom:3px;border-top:1px dashed rgba(255,255,255,.35)}
.nav{top:90px;font-family:'Cinzel',serif;font-size:16px;color:var(--white);letter-spacing:.8px;font-weight:600}
.logo-box{left:128px;top:30px;width:239px;height:108px;background:var(--white);box-shadow:0 2px 6px rgba(0,0,0,.35);display:flex;align-items:center;justify-content:center;gap:8px}
.logo-dot{width:16px;height:16px;background:var(--red)}
.logo-name{font-family:'Cinzel',serif;font-weight:600;font-size:17px;line-height:1.15;color:var(--navy);text-align:left}
.slider{left:128px;top:160px;width:943px;height:299px;box-shadow:0 4px 8px rgba(0,0,0,.3);background:linear-gradient(100deg,#2f3a45 0%,#4c6b7d 25%,#8fa7b5 45%,#c9c1ba 65%,#d8d6de 100%)}
.arrow{width:32px;height:32px;border-radius:50%;background:rgba(230,230,230,.85);top:286px}
.tag-bar{left:128px;top:480px;width:943px;height:65px;background:linear-gradient(90deg,#f9f8f6,#ffffff 60%,#f0efec);border-radius:6px;box-shadow:0 1px 3px rgba(0,0,0,.15)}
.tagline{left:144px;top:486px;font-family:'Cinzel',serif;font-size:21px;line-height:25px;color:var(--navy);letter-spacing:.5px}
.cta{left:798px;top:491px;width:252px;height:47px;background:linear-gradient(#2b86c8,var(--blue-btn));border-radius:4px;box-shadow:0 1px 2px rgba(0,0,0,.3);color:var(--white);font-weight:700;font-size:23px;display:flex;align-items:center}
.cta svg{margin:0 8px 0 10px}
.cta .sep{width:1px;height:36px;background:rgba(255,255,255,.4);margin-right:8px}
.panel{top:585px;height:307px;background:var(--panel);border:1px solid #ddd;box-shadow:0 1px 3px rgba(0,0,0,.15)}
.tab{top:582px;height:30px;background:var(--navy);color:var(--white);font-family:'Cinzel',serif;font-size:16px;letter-spacing:.6px;display:flex;align-items:center;justify-content:center;border-radius:0 0 3px 3px;box-shadow:0 1px 2px rgba(0,0,0,.3)}
.photo{background:linear-gradient(90deg,#6e9b6a 0%,#b9cbc3 30%,#d2d8d6 50%,#3b3f46 62%,#2c3038 75%,#a6b3b6 100%)}
.body-text{font-size:14.3px;line-height:20px;color:#444}
.btn-red{height:25px;background:var(--red);color:var(--white);font-size:14px;display:flex;align-items:center;justify-content:center;border-radius:6px 6px 0 0}
.post-title{font-size:15px;color:#444}
.post-date{font-size:14px;color:var(--red)}
.post-text{font-size:14px;line-height:19px;color:#444}
.post-text .more{color:var(--muted)}
.thumb{width:112px;height:90px;border:3px solid #fff;box-shadow:0 0 0 1px #ccc;background:linear-gradient(#8fb4d8 0 35%,#3f5e64 35% 75%,#7a6a38 75%)}
.divider{left:467px;top:741px;width:269px;border-top:1px dotted #aaa}
.field{left:784px;width:272px;background:#fff;border:1px solid #ddd;font-size:12px;color:#666;padding:0 0 0 30px;display:flex;align-items:center}
.field svg{position:absolute;left:8px}
.footer-red{left:0;top:945px;width:1200px;height:6px;background:var(--red)}
.footer{left:0;top:951px;width:1200px;height:70px;background:var(--navy)}
.foot-links{left:140px;top:961px;font-size:13px;color:#fff;word-spacing:2px}
.copy{left:140px;top:992px;font-size:13.5px;color:#fff}
.follow{left:838px;top:977px;font-family:'Roboto Condensed',sans-serif;font-size:16px;color:#fff;letter-spacing:.3px;white-space:nowrap}
.social{top:970px;width:30px;height:30px;border-radius:50%;background:#fff}
</style>
</head>
<body>
<div class="abs contact-line">Contact us Today : 555-014-2280</div>
<div class="abs nav-band"></div>
<nav>
  <span class="abs nav" style="left:557px">HOME</span>
  <span class="abs nav" style="left:653px">About Us</span>
  <span class="abs nav" style="left:772px">Services</span>
  <span class="abs nav" style="left:885px">Blog</span>
  <span class="abs nav" style="left:969px">Contact Us</span>
</nav>
<div class="abs logo-box"><span class="logo-dot"></span><span class="logo-name">Northvale<br>Strategy Partners</span></div>

<div class="abs slider" role="img" aria-label="Businessman drawing a network of gears labelled with leadership values, boardroom in the background"></div>
<div class="abs arrow" style="left:136px"><svg width="32" height="32"><path d="M19 10 L12 16 L19 22" fill="none" stroke="#7d1619" stroke-width="3"/></svg></div>
<div class="abs arrow" style="left:1032px"><svg width="32" height="32"><path d="M13 10 L20 16 L13 22" fill="none" stroke="#7d1619" stroke-width="3"/></svg></div>

<div class="abs tag-bar"></div>
<div class="abs tagline">We Are A Firm Providing Services Are<br>Business Consulting &amp; Executive Coaching</div>
<div class="abs cta"><svg width="26" height="32"><path d="M2 10h10V3l12 13-12 13v-7H2z" fill="#1b2a5c" stroke="#fff" stroke-width="1.5"/></svg><span class="sep"></span>Get Started Now!</div>

<section>
  <div class="abs panel" style="left:128px;width:302px"></div>
  <div class="abs tab" style="left:150px;width:161px">Welcome to NSP</div>
  <div class="abs photo" style="left:143px;top:623px;width:273px;height:141px" role="img" aria-label="Smiling businesswoman in a dark suit in a bright office corridor"></div>
  <p class="abs body-text" style="left:144px;top:771px;width:280px">Lorem ipsum dolor sit amet, consectetuer adipiscing elit, sed diam nonumibh euismod tcidunt ut laoreet dolore magna aliquam erat volutpat. Ut wisi enim ad minim veniam, quis nostrud exerci tation.</p>
  <div class="abs btn-red" style="left:323px;top:872px;width:92px">Read More</div>
</section>

<section>
  <div class="abs panel" style="left:448px;width:302px"></div>
  <div class="abs tab" style="left:470px;width:161px">Blog Posts</div>
  <div class="abs thumb" style="left:461px;top:625px" role="img" aria-label="Two-storey family house among autumn trees"></div>
  <div class="abs post-title" style="left:583px;top:627px">Ut tellus dolor dapib</div>
  <div class="abs post-date" style="left:583px;top:646px">01.01.2016</div>
  <p class="abs post-text" style="left:584px;top:664px;width:165px">Utm tellus doloribus eget, elemen velmki cursu itas. Aenean auctorbbni <span class="more">&nbsp;[...]</span></p>
  <div class="abs divider"></div>
  <div class="abs thumb" style="left:461px;top:761px" role="img" aria-label="Two-storey family house among autumn trees"></div>
  <div class="abs post-title" style="left:583px;top:763px">Ut tellus dolor dapib</div>
  <div class="abs post-date" style="left:583px;top:782px">01.01.2016</div>
  <p class="abs post-text" style="left:584px;top:800px;width:165px">Utm tellus doloribus eget, elemen velmki cursu itas. Aenean auctorbbni <span class="more">&nbsp;[...]</span></p>
  <div class="abs btn-red" style="left:643px;top:872px;width:92px">Read More</div>
</section>

<section>
  <div class="abs panel" style="left:768px;width:302px"></div>
  <div class="abs tab" style="left:790px;width:161px">Quick Inquiry</div>
  <div class="abs field" style="top:630px;height:34px"><svg width="14" height="14"><circle cx="7" cy="4" r="3" fill="#888"/><path d="M1 13c0-4 12-4 12 0z" fill="#888"/></svg>Name</div>
  <div class="abs field" style="top:671px;height:34px"><svg width="14" height="14"><rect x="1" y="3" width="12" height="8" fill="none" stroke="#888"/><path d="M1 3l6 5 6-5" fill="none" stroke="#888"/></svg>Email</div>
  <div class="abs field" style="top:714px;height:138px;align-items:flex-start;padding-top:9px"><svg width="14" height="14" style="top:8px"><rect x="1" y="3" width="10" height="10" fill="none" stroke="#888"/><path d="M6 8l7-7" stroke="#888" stroke-width="1.5"/></svg>Message</div>
  <div class="abs btn-red" style="left:963px;top:872px;width:92px">Submit</div>
</section>

<footer>
  <div class="abs footer-red"></div>
  <div class="abs footer"></div>
  <div class="abs foot-links">Home &nbsp;| &nbsp;About Us &nbsp;| &nbsp;Services &nbsp;| &nbsp;Blog &nbsp;| &nbsp;Contact Us</div>
  <div class="abs copy">© 2016 Northvale Strategy Partners All Rights Reserved</div>
  <div class="abs follow">FOLLOW US</div>
  <span class="abs social" style="left:924px"></span>
  <span class="abs social" style="left:962px"></span>
  <span class="abs social" style="left:1000px"></span>
  <span class="abs social" style="left:1038px"></span>
</footer>
</body>
</html>
```